Sophisticated, clean website reflecting my feminine, playful side to sell my abstract art,

I need a website no more than 3 pages to showcase my paintings, a little about me and some contact info. I do abstracts so looking for something a little edgy, yet feminine and current.
Updates

Hi there, These are some artists websites that I Iike: Marnelvoss.com (I like how airy it is) peterwallombry.com garethpolvens.com (I like how it scrolls) I'll need a place for a photo ( a headshot-i do not have it yet so I'll need to be able to upload that later) as well as an area for my bio. Also, it's important that I will be able to upload any new photos and descriptions easily so it should be user friendly. Lastly, I like in a sunny place so would like to have this seem upbeat and playful as that is how i like to paint. thanks-I'm trying to upload my photos now -

Target Market(s)

ppl ages 35-70 who want large scale art for their homes

Industry/Entity Type

art

Coding

Coded - Design and coding required

Number of Pages Required

3 page

Colors

Designer to choose colors to be used in the design.

Requirements
Must have
• photos of my art, a place for my bio, be easy to reach me. tasteful-nothing too "in your face" -my clients are pretty high end and organized. They like clean lines
Nice to have
• sophisticated background, muted tones in the back-similar clean font throughout-no cursive
Should not have
• too many dark areas. Too many blocks of color. Too serious.

```html
<!DOCTYPE html>
<html lang="en">
<head>
<meta charset="utf-8">
<title>Lena Corvell Art</title>
<link href="https://fonts.googleapis.com/css2?family=Playfair+Display:wght@700;800&family=Lato:wght@400;700;900&display=swap" rel="stylesheet">
<style>
:root{
  --pink:#f25fae;
  --pink-deep:#e0449a;
  --ink:#111111;
  --text:#333333;
  --muted:#666666;
  --paper:#ffffff;
  --soft:#f3f3f3;
  --line:#9a9a9a;
}
*{box-sizing:border-box;margin:0;padding:0}
html,body{width:1200px;height:3526px;overflow:hidden}
body{position:relative;background:var(--paper);font-family:"Lato",sans-serif;color:var(--text)}
.abs{position:absolute}
.serif{font-family:"Playfair Display",serif;font-weight:800}
.pink{color:var(--pink)}

/* hero */
.hero-art{left:0;top:0;width:1200px;height:700px;
  background:radial-gradient(circle at 20% 45%,#c04aa0 0,transparent 22%),radial-gradient(circle at 70% 60%,#b9469a 0,transparent 25%),radial-gradient(circle at 85% 15%,#c65aa8 0,transparent 18%),linear-gradient(180deg,#e48ccc,#df7fc4 60%,#d970bd)}
.nav{left:112px;top:48px;width:976px;height:62px;background:#fff;border-radius:31px;box-shadow:0 4px 14px rgba(0,0,0,.15)}
.brand{display:flex;align-items:center;gap:10px;font-size:27px;color:var(--ink)}
.brand-dot{width:22px;height:22px;border-radius:50%;background:var(--pink)}
.nav .brand{position:absolute;left:18px;top:14px}
.nav-links{position:absolute;left:352px;top:22px;display:flex;gap:55px;font-size:15px;color:var(--ink)}
.nav-links .active{color:var(--pink);text-decoration:underline}
.call{position:absolute;right:20px;top:8px;height:44px;width:165px;border-radius:6px 22px 22px 6px;background:var(--pink);color:#fff;font-weight:700;font-size:15px;display:flex;align-items:center;justify-content:center;gap:8px}
.hero-title{left:0;top:215px;width:1200px;text-align:center;color:#fff;font-size:74px;line-height:78px}
.hero-sub{left:220px;top:382px;width:760px;text-align:center;color:#fff;font-size:15px;line-height:29px}
.btn{display:flex;align-items:center;justify-content:center;background:#fff;color:var(--pink);font-weight:700;font-size:20px;border-radius:28px 4px 28px 4px;box-shadow:3px 3px 0 rgba(0,0,0,.35)}
.btn.solid{background:var(--pink);color:#fff}

.section-title{left:0;width:1200px;text-align:center;font-size:46px;color:var(--ink)}

/* cards */
.card{top:869px;width:296px;height:376px;border:1px solid #ddd;border-radius:14px;overflow:hidden;background:#fff;text-align:center}
.card.lift{box-shadow:0 6px 16px rgba(0,0,0,.18)}
.card-img{height:236px}
.like{position:absolute;top:15px;right:16px;background:#fff;border-radius:12px;padding:3px 9px;font-size:12px;font-weight:900;color:var(--ink)}
.like b{color:#e8334a}
.card-tag{margin-top:22px;font-size:10px;color:var(--pink);font-weight:700}
.card-name{margin-top:6px;font-size:23px;color:var(--ink)}
.card-text{margin:8px 24px 0;font-size:13px;line-height:24px;color:var(--muted)}
.arrow{width:34px;height:34px;border-radius:50%;top:1040px}

/* about */
.about-art{left:0;top:1338px;width:1200px;height:652px;
  background:radial-gradient(circle at 10% 30%,#3c4a46 0,transparent 20%),radial-gradient(circle at 90% 70%,#3b8f5e 0,transparent 22%),radial-gradient(circle at 75% 10%,#6bc07a 0,transparent 18%),linear-gradient(135deg,#b9bdc3,#8fb89a 50%,#c6c8cc)}
.about-box{left:190px;top:1434px;width:820px;height:461px;background:rgba(255,255,255,.86);border:1px solid var(--pink);text-align:center}
.about-box h2{margin-top:60px;font-size:44px;color:var(--ink)}
.about-box p{margin:22px 50px 0;font-size:15px;line-height:31px;color:var(--text)}
.about-box .btn{margin:24px auto 0;width:160px;height:54px}

/* gallery */
.gallery-bg{left:0;top:1990px;width:1200px;height:534px;background:linear-gradient(180deg,#fff,#f7f7fa)}
.g{position:absolute}
.g.hl{border:2px solid var(--pink);box-shadow:0 4px 12px rgba(0,0,0,.2)}
.insta{left:772px;top:2155px;width:26px;height:26px;border-radius:7px;background:var(--pink);border:2px solid #fff}

/* contact */
.contact-bg{left:0;top:2524px;width:1200px;height:640px;background:var(--soft)}
.c-icon{width:62px;height:62px;border-radius:50%;background:var(--pink);display:flex;align-items:center;justify-content:center}
.c-label{font-family:"Playfair Display",serif;font-weight:800;font-size:17px;color:var(--ink)}
.c-text{font-size:15px;line-height:27px;color:var(--text);margin-top:4px}
.form-head{left:561px;top:2688px;font-size:17px}
.field{border-bottom:1px solid var(--line);font-size:12px;color:var(--ink);padding-left:9px}

/* footer */
.footer{left:0;top:3150px;width:1200px;height:376px;background:#000}
.foot-brand{left:0;top:3238px;width:1200px;justify-content:center;color:#fff;font-size:42px}
.foot-brand .brand-dot{width:28px;height:28px}
.foot-nav{left:0;top:3331px;width:1200px;display:flex;justify-content:center;gap:66px;color:#fff;font-weight:700;font-size:16px}
.social{top:3382px;width:32px;height:32px;border-radius:50%;border:2px solid var(--pink)}
.copy{left:0;top:3452px;width:1200px;text-align:center;color:#fff;font-size:11px}
</style>
</head>
<body>

<!-- HERO -->
<div class="abs hero-art" role="img" aria-label="Pink abstract painting with splashes of magenta and violet"></div>
<svg class="abs" style="left:0;top:600px" width="1200" height="120" viewBox="0 0 1200 120" aria-hidden="true">
  <path d="M0 70 L60 60 L110 78 L180 58 L260 74 L330 56 L420 72 L500 60 L580 76 L660 58 L740 70 L820 55 L900 72 L980 60 L1060 74 L1130 58 L1200 66 L1200 120 L0 120Z" fill="#fff"/>
</svg>

<header class="abs nav">
  <div class="brand serif"><span class="brand-dot"></span>Lena Corvell Art</div>
  <nav class="nav-links"><span class="active">Home</span><span>About</span><span>My Painting</span><span>Contact Us</span></nav>
  <div class="call">
    <svg width="14" height="14" viewBox="0 0 24 24"><path d="M6.6 10.8a15 15 0 0 0 6.6 6.6l2.2-2.2a1 1 0 0 1 1-.25 11.4 11.4 0 0 0 3.6.57 1 1 0 0 1 1 1V20a1 1 0 0 1-1 1A17 17 0 0 1 3 4a1 1 0 0 1 1-1h3.5a1 1 0 0 1 1 1c0 1.25.2 2.45.57 3.6a1 1 0 0 1-.25 1z" fill="#fff"/></svg>
    +1 888 888 8888
  </div>
</header>

<h1 class="abs hero-title serif">Welcome To<br>Lena Corvell Art</h1>
<p class="abs hero-sub">Itaque earum rerum hic tenetur a sapiente delectus, ut aut reiciendis voluptatibus maiores alias consequatur aut perferendis doloribus asperiores repellat.</p>
<div class="abs btn" style="left:520px;top:454px;width:160px;height:55px">Get Started</div>

<!-- MY PAINTING -->
<h2 class="abs section-title serif" style="top:764px">My <span class="pink">Painting</span></h2>

<div class="abs arrow" style="left:33px;background:#777">
  <svg width="34" height="34" viewBox="0 0 34 34"><path d="M19 10 L12 17 L19 24" stroke="#fff" stroke-width="4" fill="none"/></svg>
</div>
<div class="abs arrow" style="left:1129px;background:#000">
  <svg width="34" height="34" viewBox="0 0 34 34"><path d="M15 10 L22 17 L15 24" stroke="#fff" stroke-width="4" fill="none"/></svg>
</div>

<article class="abs card" style="left:112px">
  <div class="card-img" role="img" aria-label="Painting: teal vertical band between cream drips on blue-grey" style="background:linear-gradient(90deg,#8d9bb5 0,#8d9bb5 22%,#e8e1d2 22%,#e8e1d2 34%,#1a8a80 34%,#1a8a80 66%,#e8e1d2 66%,#e8e1d2 80%,#28345a 80%)"></div>
  <span class="like"><b>&#9829;</b> 12</span>
  <div class="card-tag">Blanditiis &#10003;</div>
  <h3 class="card-name serif">Lena Corvell Art</h3>
  <p class="card-text">Nam libero tempore, cum soluta nobis est eligendi optio cumque.</p>
</article>

<article class="abs card lift" style="left:453px">
  <div class="card-img" role="img" aria-label="Painting: dark floral burst on green and white" style="background:radial-gradient(circle at 50% 45%,#2a2f2c 0,#2a2f2c 12%,transparent 30%),linear-gradient(135deg,#3f9a5a,#e8ece6 45%,#4aa06a 70%,#d8ddd8)"></div>
  <span class="like"><b>&#9829;</b> 74</span>
  <div class="card-tag">Lorem Ipsum &#10003;</div>
  <h3 class="card-name serif">Lena Corvell Art</h3>
  <p class="card-text">Itaque earum rerum hic tenetur a sapiente delectus, ut aut reiciendis</p>
</article>

<article class="abs card" style="left:793px">
  <div class="card-img" role="img" aria-label="Painting: pale canvas with blue drips on wood" style="background:linear-gradient(90deg,#8a6b50 0,#8a6b50 18%,#eeeae2 18%,#c7d9ec 50%,#eeeae2 82%,#8a6b50 82%)"></div>
  <span class="like"><b>&#9829;</b> 31</span>
  <div class="card-tag">Voluptem Sans &#10003;</div>
  <h3 class="card-name serif">Lena Corvell Art</h3>
  <p class="card-text">Nam libero tempore, cum soluta nobis est eligendi optio cumque.</p>
</article>

<!-- ABOUT -->
<div class="abs about-art" role="img" aria-label="Abstract painting in greens, greys and black strokes"></div>
<section class="abs about-box">
  <h2 class="serif">About Lena Corvell <span class="pink">Art</span></h2>
  <p>Et harum quidem rerum facilis est et expedita distinctio. Nam libero tempore, cum soluta nobis est eligendi optio cumque nihil impedit quo minus id quod maxime placeat facere possimus, omnis voluptas assumenda est, omnis dolor repellendus. Temporibus autem quibusdam et aut officiis debitis aut rerum necessitatibus saepe eveniet ut et voluptates repudiandae sint et molestiae non recusandae. Itaque earum rerum hic tenetur a sapiente delectus, ut aut reiciendis voluptatibus maiores alias consequatur aut perferendis doloribus asperiores repellat.</p>
  <div class="btn solid">Read More</div>
</section>

<!-- GALLERY -->
<div class="abs gallery-bg"></div>
<h2 class="abs section-title serif" style="top:2055px">Our <span class="pink">Gallery</span></h2>

<div class="g" role="img" aria-label="Painting: blue drips on cream" style="left:0;top:2168px;width:148px;height:263px;background:linear-gradient(90deg,#eeeae2,#c7d9ec 60%,#8a6b50 88%)"></div>
<div class="g" role="img" aria-label="Painting: dark floral on green" style="left:166px;top:2212px;width:132px;height:170px;background:linear-gradient(135deg,#3f9a5a,#e6ebe5 50%,#2a3a30)"></div>
<div class="g" role="img" aria-label="Painting: violet flower bursts" style="left:312px;top:2168px;width:204px;height:263px;background:linear-gradient(135deg,#d8cfcf,#7b5c8f 50%,#cfc6c9)"></div>
<div class="g" role="img" aria-label="Painting: gold and blue swirls" style="left:534px;top:2212px;width:132px;height:170px;background:linear-gradient(135deg,#c99a3a,#e9e4d8 50%,#5d78a8)"></div>
<div class="g hl" role="img" aria-label="Painting: teal band with dark drips" style="left:683px;top:2168px;width:202px;height:263px;background:linear-gradient(90deg,#e8e1d2 0,#e8e1d2 20%,#1a8a80 20%,#1a8a80 80%,#e8e1d2 80%)"></div>
<div class="abs insta"></div>
<div class="g" role="img" aria-label="Painting: rose tones on cream" style="left:904px;top:2212px;width:133px;height:170px;background:linear-gradient(135deg,#5a3a32,#e8d8d0 50%,#a36a5a)"></div>
<div class="g" role="img" aria-label="Painting: blue and yellow strokes" style="left:1053px;top:2168px;width:147px;height:263px;background:linear-gradient(135deg,#4a6fc0,#e8e6de 45%,#d8b83a 70%,#2a2a2a)"></div>

<!-- CONTACT -->
<div class="abs contact-bg"></div>
<h2 class="abs section-title serif" style="top:2586px">Get <span class="pink">In Touch</span></h2>

<div class="abs c-icon" style="left:111px;top:2708px">
  <svg width="22" height="22" viewBox="0 0 24 24"><path d="M12 2a7 7 0 0 0-7 7c0 5 7 13 7 13s7-8 7-13a7 7 0 0 0-7-7zm0 9.5A2.5 2.5 0 1 1 12 6.5a2.5 2.5 0 0 1 0 5z" fill="#fff"/></svg>
</div>
<div class="abs" style="left:193px;top:2705px;width:290px">
  <div class="c-label">LOCATION</div>
  <div class="c-text">123 Lorem ipsum dolor sit amet conse ctetur adipiscing elit.</div>
</div>

<div class="abs c-icon" style="left:111px;top:2832px">
  <svg width="22" height="22" viewBox="0 0 24 24"><path d="M6.6 10.8a15 15 0 0 0 6.6 6.6l2.2-2.2a1 1 0 0 1 1-.25 11.4 11.4 0 0 0 3.6.57 1 1 0 0 1 1 1V20a1 1 0 0 1-1 1A17 17 0 0 1 3 4a1 1 0 0 1 1-1h3.5a1 1 0 0 1 1 1c0 1.25.2 2.45.57 3.6a1 1 0 0 1-.25 1z" fill="#fff"/></svg>
</div>
<div class="abs" style="left:192px;top:2841px">
  <div class="c-label">PHONE NUMBER</div>
  <div class="c-text">+1 888 888 8888</div>
</div>

<div class="abs c-icon" style="left:111px;top:2949px">
  <svg width="22" height="22" viewBox="0 0 24 24"><path d="M3 6h18v12H3z" fill="#fff"/><path d="M3 6l9 7 9-7" stroke="#f25fae" stroke-width="2" fill="none"/></svg>
</div>
<div class="abs" style="left:192px;top:2955px">
  <div class="c-label">EMAIL ADDRESS</div>
  <div class="c-text">info@lenacorvellart.com</div>
</div>

<div class="abs form-head c-label">SEND US A MESSAGE</div>
<div class="abs field" style="left:561px;top:2748px;width:252px;height:37px">Your Name</div>
<div class="abs field" style="left:826px;top:2748px;width:260px;height:37px">Email</div>
<div class="abs field" style="left:561px;top:2816px;width:252px;height:37px">Phone Number</div>
<div class="abs field" style="left:826px;top:2816px;width:260px;height:37px">Subject</div>
<div class="abs field" style="left:561px;top:2885px;width:525px;height:55px">Message</div>
<div class="abs btn solid" style="left:561px;top:2975px;width:142px;height:55px">Submit</div>

<!-- FOOTER -->
<svg class="abs" style="left:0;top:3080px" width="1200" height="80" viewBox="0 0 1200 80" aria-hidden="true">
  <path d="M0 60 L70 40 L140 55 L220 30 L300 48 L380 35 L460 50 L540 28 L620 45 L700 32 L780 50 L860 30 L940 46 L1020 34 L1100 50 L1200 38 L1200 80 L0 80Z" fill="#000"/>
</svg>
<footer class="abs footer"></footer>
<div class="abs brand serif foot-brand" style="display:flex"><span class="brand-dot"></span>Lena Corvell Art</div>
<nav class="abs foot-nav"><span>HOME</span><span>MY PAINTINGS</span><span>ABOUT ME</span><span>GALLERY</span><span>CONTACT ME</span></nav>
<div class="abs social" style="left:511px" aria-label="Social link 1"></div>
<div class="abs social" style="left:560px" aria-label="Social link 2"></div>
<div class="abs social" style="left:608px" aria-label="Social link 3"></div>
<div class="abs social" style="left:657px" aria-label="Social link 4"></div>
<p class="abs copy">&copy; copyrights 2022 Lena Corvell Art &nbsp;| &nbsp;&nbsp;All rights reserved.</p>

</body>
</html>
```